Phuket Thailand - Rental Villa Website

I have a villa for rent in Thailand and require a website - i need to demo pictures/walk through video, local attractions, villa facilities description plus seaonal rates and online booking.

Industry/Entity Type

Rental

Coding

Coded - Design and coding required

```html
<!DOCTYPE html>
<html lang="en">
<head>
<meta charset="utf-8">
<title>Kata Bay Villa</title>
<link rel="stylesheet" href="https://fonts.googleapis.com/css2?family=Oswald:wght@300;400;500&family=Open+Sans:wght@400;600&display=swap">
<style>
:root{
  --green:#07920a;
  --ink:#1b1b1b;
  --body:#555;
  --white:#fff;
  --footer:#000;
  --rule:#bbb;
  --hero-top:#6f9fbf;
  --hero-bottom:#3f6a48;
  --sea:#7cc8e8;
  --sea-light:#9ad9f2;
  --tile:#8fa9a6;
}
*{margin:0;padding:0;box-sizing:border-box}
html,body{width:810px;height:1200px;overflow:hidden;background:var(--white);font-family:'Open Sans',sans-serif}
.page{position:relative;width:810px;height:1200px}
.hero-photo{position:absolute;left:0;top:0;width:810px;height:562px;background:linear-gradient(180deg,var(--hero-top),var(--hero-bottom))}
.logo{position:absolute;left:14px;top:26px;display:flex;align-items:center;gap:8px}
.logo-dot{width:34px;height:34px;border-radius:50%;background:#f5a623}
.logo-name{font-family:'Oswald',sans-serif;font-weight:500;font-size:24px;color:var(--white);letter-spacing:1px}
.nav{position:absolute;top:24px;left:0;width:810px;height:28px}
.nav a{position:absolute;top:0;height:28px;line-height:28px;font-size:13.5px;color:var(--ink);text-decoration:none}
.nav a.active{color:var(--green);border:1px solid var(--white);background:rgba(255,255,255,.25);width:68px;text-align:center}
.hero-title{position:absolute;top:152px;left:0;width:810px;line-height:50px;text-align:center;font-family:'Oswald',sans-serif;font-size:38px;color:var(--white);font-weight:400}
.hero-rule{position:absolute;top:206px;left:314px;width:188px;height:3px;background:var(--white)}
.hero-text{position:absolute;top:220px;left:215px;width:380px;text-align:center;font-family:'Oswald',sans-serif;font-weight:400;font-size:16px;line-height:21px;color:var(--white)}
.booking{position:absolute;top:361px;left:0}
.field{position:absolute;top:0;width:176px;height:24px;background:var(--white);font-size:11px;color:#999;line-height:24px;padding-left:5px}
.book-btn{position:absolute;top:0;left:651px;width:76px;height:24px;background:var(--green);color:var(--white);font-family:'Oswald',sans-serif;font-size:14.5px;line-height:24px;text-align:center}
.welcome{position:absolute;left:52px;top:440px;width:706px;height:220px;background:var(--white);border-top:5px solid var(--green)}
.section-title{position:absolute;left:0;width:810px;text-align:center;font-family:'Oswald',sans-serif;font-weight:400;font-size:24px;line-height:32px;color:var(--ink)}
.section-title span{color:var(--green)}
.divider{position:absolute;left:317px;width:176px;height:20px}
.copy{position:absolute;left:102px;width:607px;text-align:center;font-size:10.5px;line-height:15.6px;color:var(--body)}
.attractions{position:absolute;left:0;top:682px;width:810px;height:246px;background:linear-gradient(180deg,var(--sea),var(--sea-light))}
.tile{position:absolute;top:56px;width:162px;height:162px;background:var(--tile)}
.rates{position:absolute;left:52px;top:995px;width:706px;border-collapse:collapse;table-layout:fixed;color:var(--green)}
.rates th{background:var(--green);color:var(--white);font-weight:400;font-size:17.5px;height:34px;border:1px solid var(--white)}
.rates td{font-size:14.5px;height:32px;text-align:center;border:1px solid var(--green)}
.rates th:first-child,.rates td:first-child{text-align:left;padding-left:12px}
.footer{position:absolute;left:0;top:1152px;width:810px;height:48px;background:var(--footer);border-top:4px solid var(--green)}
.footer a,.footer p{position:absolute;top:15px;font-size:11px;color:var(--white);text-decoration:none}
.footer a.active,.footer p span{color:var(--green)}
</style>
</head>
<body>
<div class="page">
  <div class="hero-photo" role="img" aria-label="Photo of a tropical bay with beach and palm-covered hills"></div>

  <div class="logo"><span class="logo-dot"></span><span class="logo-name">KATA BAY VILLA</span></div>

  <nav class="nav">
    <a class="active" href="#" style="left:342px">Home</a>
    <a href="#" style="left:425px">About</a>
    <a href="#" style="left:486px">Gallery</a>
    <a href="#" style="left:559px">Attraction</a>
    <a href="#" style="left:658px">Enquiry</a>
    <a href="#" style="left:735px">Contact</a>
  </nav>

  <h1 class="hero-title">KATA BAY VILLA</h1>
  <div class="hero-rule"></div>
  <p class="hero-text">Lorem Ipsum is simply dummy text of the printing and typesetting industry. Lorem Ipsum has been the industry's standard dummy text ever since the 1500.</p>

  <div class="booking">
    <div class="field" style="left:82px">Select Package</div>
    <div class="field" style="left:271px">Departure Date</div>
    <div class="field" style="left:461px">Arrival Date</div>
    <div class="book-btn">Book Now</div>
  </div>

  <section class="welcome"></section>
  <h2 class="section-title" style="top:466px"><span>Welcome to</span> KATA BAY VILLA</h2>
  <svg class="divider" style="top:502px" viewBox="0 0 176 20">
    <line x1="0" y1="10" x2="70" y2="10" stroke="var(--rule)"/>
    <line x1="105" y1="10" x2="176" y2="10" stroke="var(--rule)"/>
    <path d="M88 1 L98 10 H95 V18 H90.5 V13 H85.5 V18 H81 V10 H78 Z" fill="var(--green)"/>
  </svg>
  <p class="copy" style="top:526px">Lorem Ipsum is simply dummy text of the printing and typesetting industry. Lorem Ipsum has been the industry's standard dummy text ever since the 1500s, when an unknown printer took a galley of type and scrambled it to make a type specimen book. It has survived not only five centuries, but also the leap into electronic typesetting, remaining essentially unchanged. It was popularised in the 1960s with the release of Letraset sheets containing Lorem Ipsum passages, and more recently with desktop publishing software like Aldus PageMaker including versions of Lorem Ipsum.</p>
  <p class="copy" style="top:619px">Lorem Ipsum is simply dummy text of the printing and typesetting industry. Lorem Ipsum has been the industry's standard dummy text ever since the 1500s, when an unknown printer took a galley of type and scrambled.</p>

  <section class="attractions" role="img" aria-label="Photo of sea water as section background">
    <h2 class="section-title" style="top:2px"><span>Local</span> Attraction</h2>
    <svg class="divider" style="top:34px" viewBox="0 0 176 20">
      <line x1="2" y1="10" x2="72" y2="10" stroke="var(--green)"/>
      <line x1="103" y1="10" x2="173" y2="10" stroke="var(--green)"/>
      <path d="M88 1 a6 6 0 0 1 6 6 c0 5 -6 12 -6 12 s-6 -7 -6 -12 a6 6 0 0 1 6 -6 z" fill="var(--green)"/>
      <circle cx="88" cy="7" r="2.3" fill="var(--sea)"/>
    </svg>
    <div class="tile" style="left:0" role="img" aria-label="Photo of a lagoon between limestone cliffs"></div>
    <div class="tile" style="left:162px" role="img" aria-label="Photo of a busy island beach"></div>
    <div class="tile" style="left:324px" role="img" aria-label="Photo of a temple pavilion by a pond"></div>
    <div class="tile" style="left:486px" role="img" aria-label="Photo of a sun lounger on a beach"></div>
    <div class="tile" style="left:648px" role="img" aria-label="Photo of a historic square with a fountain"></div>
  </section>

  <h2 class="section-title" style="top:932px"><span>Seasonal</span> Rates</h2>
  <svg class="divider" style="top:968px" viewBox="0 0 176 20">
    <line x1="0" y1="10" x2="70" y2="10" stroke="var(--rule)"/>
    <line x1="105" y1="10" x2="176" y2="10" stroke="var(--rule)"/>
    <rect x="80" y="3" width="16" height="15" rx="1" fill="none" stroke="var(--green)" stroke-width="2"/>
    <rect x="80" y="3" width="16" height="4" fill="var(--green)"/>
    <path d="M83 10h2v2h-2zM87 10h2v2h-2zM91 10h2v2h-2zM83 14h2v2h-2zM87 14h2v2h-2zM91 14h2v2h-2z" fill="var(--green)"/>
  </svg>

  <table class="rates">
    <colgroup><col style="width:171px"><col><col><col><col><col></colgroup>
    <tr><th>Seasonal rates</th><th>max. occ.</th><th>Christmas</th><th>Winter</th><th>Summer</th><th>normal</th></tr>
    <tr><td>standard</td><td>2</td><td>$140</td><td>$120</td><td>$110</td><td>$100</td></tr>
    <tr><td>Superior</td><td>2</td><td>$180</td><td>$160</td><td>$150</td><td>$140</td></tr>
    <tr><td>Delux</td><td>2+1</td><td>$240</td><td>$220</td><td>$200</td><td>$190</td></tr>
  </table>

  <footer class="footer">
    <a class="active" href="#" style="left:63px">Home</a>
    <a href="#" style="left:125px">About</a>
    <a href="#" style="left:186px">Gallery</a>
    <a href="#" style="left:253px">Attraction</a>
    <a href="#" style="left:335px">Enquiry</a>
    <a href="#" style="left:405px">Contact</a>
    <p style="left:514px">© <span>KATA BAY VILLA</span> - 2015. All Rights Reserved.</p>
  </footer>
</div>
</body>
</html>
```